Flyer-Design für Elektriker
Zielgruppe
Wir sind ein Handwerksunternehemen im Bereich Elektrotechnik.
Wir sind speziell im Neubau und bei Sanierungen im Einsatz. Eh
Es wird ein passender Flyer für potentielle Neukkunden benötigt.
Der Gewinner soll uns im Anschluss zwei weitere Flyer für andere Themenbereiche erstellen!
Aufgabenstellung
Wir wünschen uns einen professionellen Flyer.
Unsere Vorgaben können gerne kreativ geändert werden.
Stockbilder evtl. passend zum Neubau / Sanierung können verwendet werden.
Bitte die Druckvorlagen beachten von Druck blitz
Im Anhang sind noch zwei Flyer von anderen Unternehmen. So in der Art stellen wir uns den Flyer vor.
Im Anhang:

```html
<!DOCTYPE html>
<html lang="de">
<head>
<meta charset="utf-8">
<title>Flyer – Sie kennen es bestimmt</title>
<link rel="stylesheet" href="https://fonts.googleapis.com/css2?family=Open+Sans:wght@400;600&display=swap">
<style>
  :root {
    --blue-dark: #206fa1;
    --blue-deep: #225f8d;
    --blue-light: #339fdd;
    --blue-bright: #1fa5f0;
    --blue-mid: #1c7fb5;
    --text: #222222;
    --white: #ffffff;
  }
  * { margin: 0; padding: 0; box-sizing: border-box; }
  html, body { width: 849px; height: 1200px; overflow: hidden; background: var(--white); }
  .flyer {
    position: relative;
    width: 849px;
    height: 1200px;
    font-family: "Open Sans", sans-serif;
    color: var(--text);
    background: var(--white);
  }
  .header-shape {
    position: absolute;
    left: 0; top: 0;
    width: 849px; height: 320px;
  }
  .title {
    position: absolute;
    top: 64px; left: 0; width: 100%;
    text-align: center;
    color: var(--white);
    font-weight: 600;
    font-size: 44px;
    letter-spacing: 0.3px;
  }
  .title-icon {
    position: absolute;
    left: 361px; top: 144px;
    width: 100px; height: 98px;
    background: linear-gradient(160deg, rgba(255,255,255,0.35), rgba(255,255,255,0.15));
    border-radius: 8px;
  }
  .problems {
    position: absolute;
    left: 53px; top: 312px;
    width: 780px;
    font-size: 27.5px;
    line-height: 33px;
  }
  .problems p { margin-bottom: 19px; }
  .solution-heading {
    position: absolute;
    left: 53px; top: 791px;
    font-size: 29px;
    font-weight: 600;
    color: #1a1a1a;
  }
  .solution-icon {
    position: absolute;
    left: 273px; top: 772px;
    width: 44px; height: 56px;
    border-radius: 22px 22px 10px 10px;
    background: linear-gradient(180deg, rgba(31,165,240,0.35), rgba(31,165,240,0.15));
  }
  .solution-text {
    position: absolute;
    left: 53px; top: 835px;
    width: 780px;
    font-size: 27px;
    line-height: 32.5px;
  }
</style>
</head>
<body>
<div class="flyer">
  <svg class="header-shape" viewBox="0 0 849 320" aria-hidden="true">
    <defs>
      <linearGradient id="rightWing" x1="1" y1="0" x2="0" y2="1">
        <stop offset="0" stop-color="#1fa5f0"/>
        <stop offset="1" stop-color="#1c7fb5"/>
      </linearGradient>
      <filter id="bandShadow" x="-10%" y="-10%" width="120%" height="140%">
        <feDropShadow dx="0" dy="12" stdDeviation="14" flood-color="#000" flood-opacity="0.3"/>
      </filter>
    </defs>
    <polygon points="0,0 849,0 849,196 429,282 0,194" fill="var(--blue-dark)" filter="url(#bandShadow)"/>
    <polygon points="220,184 545,226 429,282" fill="var(--blue-deep)"/>
    <polygon points="0,86 429,282 0,194" fill="var(--blue-light)"/>
    <polygon points="849,89 849,196 429,282 545,226" fill="url(#rightWing)"/>
  </svg>

  <h1 class="title">Sie kennen es bestimmt...</h1>
  <div class="title-icon" role="img" aria-label="Icon: Kopf im Profil mit Fragezeichen und Symbolen"></div>

  <div class="problems">
    <p>• Auf der Baustelle wird vermehrt kein qualifiziertes<br>Personal von den Handwerksbetrieben eingesetzt<br>Wodurch Keine fachgerechte Ausführung gewährleistet<br>wird.</p>
    <p>•schlechte Kommunikation auf der Baustelle oder<br>sogar mit den Unternehmen führen schnell zu<br>Missverständnissen.</p>
    <p>•Durch eine Schlechte Beratung oder Ausführung<br>kommt es zu Nachträgen € und Vezögerungen.</p>
    <p>•&nbsp; Keine termingerechte Fertigstellung hat unzufriedene<br>Bauherren zur Folge.</p>
  </div>

  <h2 class="solution-heading">Unsere Lösung</h2>
  <div class="solution-icon" role="img" aria-label="Icon: Glühbirne als Symbol für eine Idee"></div>

  <div class="solution-text">
    Uns ist wichtig, dass Bauherren pünktlich in Ihr neues<br>Zuhause einziehen können mit maximaler Zufriedenheit<br>an der handwerklichen Ausführung damit unsere<br>Kunden zufriedene Auftraggeber haben.<br>Um diesen Anspruch gerecht zu werden, setzen wir nur<br>auf eigene ausgebildete Fachkräfte.
  </div>
</div>
</body>
</html>
```